Church needs a street sign design

We're a small church located in Silicon Valley, California. Our website is https://www.vgtmarlowfield.org/ and our address is 4817 Ferrow Ave, San Jose, California, 95873. You can look up our location on Google Maps to see the sign from Street View. I have uploaded an image of the street sign as well. The marquee, the top section of the sign, and the separating line between them both will be removed. We're seeking a design for a new backlit acrylic insert that will go on the front of the light box and the back of the lightbox. The acrylic sign will fill the entire external frame. In the future, we may build a decorative wood frame around the structural legs, as visualized in one of the uploaded files. The church's brand colors are: #003366 (dark blue), #ff6600 (vibrant orange), #228b22 (forest green). I have also uploaded the church's logo assets. Our primary font is Montserrat and the secondary is Poppins. You can deviate from these colors/fonts if the sign is still coherent with the rest of our branding. Our branding values are mission, truth, passion, and community (please do not put those words on the sign! They are just intended to guide the look of the design). The sign dimensions are 96" by 47.5". Keep in mind that the sign will be backlit on a busy street side. It will also be positioned next to an old-looking church building. We do NOT want a sign that looks traditional, old, or antiquated. Instead, we want a modern-looking sign that pairs well with our old building while helping it look more modern too. We would also like the web address clearly visible on the sign: vgtmarlowfield.org. If you have any questions, just let me know!

```html
<!DOCTYPE html>
<html lang="en">
<head>
<meta charset="utf-8">
<title>Valegate Marlowfield Church – Street Sign</title>
<link rel="stylesheet" href="https://fonts.googleapis.com/css2?family=Montserrat:wght@500;600;700&display=swap">
<style>
  :root {
    --navy: #003366;
    --orange: #ff6600;
    --white: #ffffff;
    --ink: #111111;
    --label-grey: #e6e6e6;
    --backdrop: #b3b3b3;
  }
  * { margin: 0; padding: 0; box-sizing: border-box; }
  html, body {
    width: 1200px; height: 1000px; overflow: hidden;
    background: var(--backdrop);
    font-family: "Montserrat", sans-serif;
  }
  .sign {
    position: absolute; left: 132px; top: 268px;
    width: 936px; height: 463px;
    background: var(--white); overflow: hidden;
  }
  .sign-shapes { position: absolute; inset: 0; width: 100%; height: 100%; }
  .brand { position: absolute; left: 345px; top: 30px; display: flex; align-items: center; gap: 26px; }
  .brand-mark { width: 52px; height: 52px; background: var(--ink); }
  .brand-name { color: var(--ink); font-weight: 600; line-height: 1; }
  .brand-name .primary { display: block; font-size: 44px; letter-spacing: 0.5px; }
  .brand-name .secondary { display: block; font-size: 15.4px; margin-top: 6px; letter-spacing: 0.3px; }
  .schedule { position: absolute; left: 90px; }
  .schedule-label {
    color: var(--label-grey); font-weight: 700; font-size: 29.5px; line-height: 1;
    letter-spacing: 0.3px;
  }
  .schedule-time {
    display: inline-block; margin-top: 4px;
    background: var(--orange); color: var(--navy);
    font-weight: 600; font-size: 27px; line-height: 33px; padding: 0 6px;
    letter-spacing: -0.5px;
  }
  .schedule--service { top: 225px; }
  .schedule--lunch { top: 314px; }
  .schedule--lunch .schedule-time { font-size: 30px; line-height: 32px; }
  .location { position: absolute; left: 484px; top: 236px; display: flex; align-items: center; gap: 24px; }
  .location-pin { width: 33px; height: 45px; flex: none; }
  .location-address {
    color: var(--white); font-weight: 600; font-size: 31.5px; line-height: 41px;
    letter-spacing: 0.4px; font-style: normal;
  }
  .web-band {
    position: absolute; left: 0; top: 402px; width: 100%; height: 43px;
    display: flex; align-items: center; justify-content: center;
    color: var(--white); font-weight: 700; font-size: 34px; letter-spacing: 0.3px;
  }
</style>
</head>
<body>
  <section class="sign" aria-label="Valegate Marlowfield Church street sign">
    <svg class="sign-shapes" viewBox="0 0 1638 810" preserveAspectRatio="none" aria-hidden="true">
      <path fill="var(--navy)" d="M0 250 C150 340 300 380 440 380 C800 380 1050 240 1299 240 C1450 240 1560 270 1638 305 L1638 810 L0 810 Z"/>
      <path fill="var(--orange)" d="M0 167 C120 270 260 315 420 315 C750 315 1100 210 1349 215 C1080 205 800 355 440 355 C260 355 120 300 0 220 Z"/>
      <rect fill="var(--orange)" x="0" y="705" width="1638" height="75"/>
    </svg>

    <div class="brand">
      <span class="brand-mark"></span>
      <h1 class="brand-name">
        <span class="primary">VALEGATE</span>
        <span class="secondary">MARLOWFIELD CHURCH</span>
      </h1>
    </div>

    <div class="schedule schedule--service">
      <p class="schedule-label">SUNDAY SERVICE</p>
      <p class="schedule-time">10:40 AM - 12:15 PM</p>
    </div>

    <div class="schedule schedule--lunch">
      <p class="schedule-label">LUNCH PROVIDED</p>
      <p class="schedule-time">12:30 PM - 1:30 PM</p>
    </div>

    <div class="location">
      <svg class="location-pin" viewBox="0 0 33 45" aria-hidden="true">
        <path fill="var(--orange)" d="M16.5 0C7.4 0 0 7.2 0 16.2c0 5 2.2 8.3 4 11L16.5 45 29 27.2c1.8-2.7 4-6 4-11C33 7.2 25.6 0 16.5 0z"/>
        <circle cx="16.5" cy="16" r="8" fill="var(--navy)"/>
      </svg>
      <address class="location-address">
        4817 Ferrow Ave,<br>
        San Jose,<br>
        California, 95873
      </address>
    </div>

    <a class="web-band" href="https://www.vgtmarlowfield.org/" style="text-decoration:none">www.vgtmarlowfield.org</a>
  </section>
</body>
</html>
```